Bright, Bold Sydney Tutoring Business Flyer Advertisment

Lumora is an up and coming tutoring business located on Sydney's Upper North Shore catering to school students of all ages. We need a flyer designed for notice boards and letter box drops to attract new clients. Our tutors are mostly university education students who are fresh, dedicated and passionate about their areas of teaching. The flyer should exhibit a bright, bold, modern, clean cut style which would appeal to both students and parents. I have attached our logo (the flyer could reflect this colour scheme), and a PDF which outlines the information we would like to appear on the flyer. This is not set in stone, but designed to act as an extremely loose guide for your creativity !

Target Market(s)

Affluent School Students and Parents

Industry/Entity Type

Tutoring

Requirements
Must have
• Logo, $10 offer, company description.
Nice to have
• Grabbing headlines to attract new clients, such as "Feeling overwhelmed at school?". We are looking for an eye catching, clean cut and professional design that has the colours to attract kids and the tone to attract parents.

```html
<!DOCTYPE html>
<html lang="en">
<head>
<meta charset="utf-8">
<title>Lumora Tutoring Flyer</title>
<link href="https://fonts.googleapis.com/css2?family=Questrial&family=Roboto+Slab:wght@500&display=swap" rel="stylesheet">
<style>
  :root {
    --stage: #e4e4e7;
    --paper: #ffffff;
    --panel-top: #f3f4f6;
    --panel-bottom: #e2e3e6;
    --ink: #1d1d1f;
    --ink-dark: #2f2f33;
    --sky: #4c9fd9;
    --rose: #e8739a;
    --footer: #050505;
    --footer-text: #f2f2f2;
  }
  * { margin: 0; padding: 0; box-sizing: border-box; }
  html, body { width: 969px; height: 1200px; overflow: hidden; background: var(--stage); }
  .canvas { position: relative; width: 969px; height: 1200px; }
  .flyer {
    position: absolute; left: 184px; top: 188px;
    width: 624px; height: 864px;
    background: var(--paper); padding: 12px;
    font-family: "Questrial", "Century Gothic", sans-serif;
    color: var(--ink);
  }
  .panel {
    position: relative; width: 600px; height: 840px;
    background: linear-gradient(180deg, var(--panel-top) 0%, #f8f8f9 45%, var(--panel-bottom) 100%);
    overflow: hidden;
  }
  .brand {
    position: absolute; left: 58px; top: 210px;
    display: flex; align-items: center; gap: 10px;
  }
  .brand-dot { width: 20px; height: 20px; border-radius: 50%; background: var(--rose); }
  .brand-name { font-size: 44px; color: var(--ink-dark); line-height: 1; }
  .headline {
    position: absolute; left: 263px;
    border-left: 3px solid var(--rose); padding-left: 8px;
    font-family: "Roboto Slab", "Rockwell", serif; font-weight: 500;
    font-size: 19px; line-height: 22px; letter-spacing: 0.5px;
    color: var(--sky); text-transform: uppercase; white-space: nowrap;
  }
  .h1 { top: 48px; } .h2 { top: 109px; } .h3 { top: 194px; }
  .description {
    position: absolute; left: 263px; top: 274px; width: 318px;
    font-size: 17px; line-height: 20px;
  }
  .offer {
    position: absolute; left: 263px; top: 416px;
    font-size: 14.5px; line-height: 16px; color: var(--sky);
    text-transform: uppercase; white-space: nowrap;
  }
  .contact-call {
    position: absolute; left: 263px; top: 455px;
    font-size: 10.5px; line-height: 12px;
    text-transform: uppercase; white-space: nowrap;
  }
  .hero {
    position: absolute; left: 0; top: 440px; width: 600px; height: 344px;
    background:
      radial-gradient(ellipse 30% 48% at 30% 58%, rgba(214,190,168,.75), rgba(214,190,168,0) 100%),
      radial-gradient(ellipse 38% 28% at 30% 90%, rgba(120,80,60,.35), rgba(120,80,60,0) 100%),
      linear-gradient(180deg, rgba(240,240,242,0), rgba(225,226,229,.6));
  }
  .footer {
    position: absolute; left: 0; bottom: 0; width: 100%; height: 56px;
    background: var(--footer); color: var(--footer-text);
    text-align: center;
  }
  .footer-row { display: flex; justify-content: center; align-items: center; gap: 6px; }
  .footer-row.primary { font-size: 16px; padding-top: 6px; }
  .footer-row.secondary { font-size: 13px; margin-top: 4px; }
  .footer-row .spacer { width: 10px; }
  .icon { width: 13px; height: 13px; flex: none; }
  .secondary .icon { width: 10px; height: 11px; }
</style>
</head>
<body>
<div class="canvas">
  <div class="flyer">
    <div class="panel">
      <div class="brand">
        <span class="brand-dot"></span>
        <span class="brand-name">Lumora</span>
      </div>

      <h2 class="headline h1">Feeling overwhelmed<br>by the HSC?</h2>
      <h2 class="headline h2">Looking to improve<br>your skills,confidence<br>and organisation?</h2>
      <h2 class="headline h3">Want to increase your<br>child’s engagement<br>at school?</h2>

      <p class="description">Lumora Tutoring offers one-on-one, individualized learning experiences to maximise academic development. Our tutors are hand selected on the basis of their qualifications, expertise and passion for inspiring young learners.</p>

      <p class="offer">Mention this advertisement to claim<br>your trial session for just $10!</p>
      <p class="contact-call">Contact us today to discuss how we can help<br>make your learning goals a reality!</p>

      <div class="hero" role="img" aria-label="Photo of a smiling young boy in a white shirt reading an open book, with letters floating out of the pages"></div>

      <footer class="footer">
        <div class="footer-row primary">
          <svg class="icon" viewBox="0 0 13 13"><rect x="0" y="0" width="13" height="13" rx="2" fill="#4c9fd9"/><rect x="2.5" y="3.5" width="8" height="6" fill="none" stroke="#050505" stroke-width="1"/><path d="M2.5 3.5 L6.5 7 L10.5 3.5" fill="none" stroke="#050505" stroke-width="1"/></svg>
          <span>info@lumoratutoring.com.au</span>
          <span class="spacer"></span>
          <svg class="icon" viewBox="0 0 13 13"><rect x="0" y="0" width="13" height="13" rx="2" fill="#4c9fd9"/><circle cx="6.5" cy="6.5" r="4" fill="none" stroke="#050505" stroke-width="1"/><path d="M2.5 6.5 H10.5 M6.5 2.5 C4.5 5 4.5 8 6.5 10.5 M6.5 2.5 C8.5 5 8.5 8 6.5 10.5" fill="none" stroke="#050505" stroke-width=".8"/></svg>
          <span>www/lumoratutoring.com.au</span>
        </div>
        <div class="footer-row secondary">
          <svg class="icon" viewBox="0 0 10 11"><rect x="0" y="0" width="10" height="11" rx="1.5" fill="#4c9fd9"/><path d="M5 9 C3 6.5 2.5 5.5 2.5 4.3 A2.5 2.5 0 0 1 7.5 4.3 C7.5 5.5 7 6.5 5 9 Z" fill="#050505"/></svg>
          <span>Suite 4, 860 Kingsway Road Lindfield, Nsw 2070</span>
        </div>
      </footer>
    </div>
  </div>
</div>
</body>
</html>
```